Health Care Company with Logo Needs Business Cards designed

We are a luxury behavioral health company looking for business cards design we already have a logo and are looking for someone to design a sophisticated luxurious looking business card. Please note that Card design should be captivating just like the logo and also encompass the logo color

Industry/Entity Type

Healthcare

Contact Information for Business Card

Logo,company name, tagline, my name and title, contact details, and physical address

```html
<!DOCTYPE html>
<html lang="en">
<head>
<meta charset="utf-8">
<title>Orin Behavioral Health – Business Cards</title>
<link rel="stylesheet" href="https://fonts.googleapis.com/css2?family=Roboto:wght@400;700;900&family=Roboto+Mono:wght@500&display=swap">
<style>
  :root {
    --bg: #e9e9e7;
    --purple: #6f3391;
    --purple-deep: #5f2a7e;
    --purple-emboss: #55246f;
    --sky: #00a8e4;
    --orange: #f08c1e;
    --green: #86bf3b;
    --white: #ffffff;
    --card-w: 520px;
    --card-h: 297px;
  }
  * { box-sizing: border-box; margin: 0; padding: 0; }
  html, body {
    width: 1200px; height: 802px; overflow: hidden;
    background: var(--bg);
    font-family: "Roboto", Arial, sans-serif;
  }
  .stage { position: relative; width: 1200px; height: 802px; }
  .card {
    position: absolute;
    width: var(--card-w); height: var(--card-h);
    background: var(--purple);
    overflow: hidden;
    box-shadow: 0 6px 18px rgba(0,0,0,0.18);
  }
  .card--front { left: 50px; top: 120px; }
  .card--back  { left: 630px; top: 385px; }

  /* front */
  .front__panel { position: absolute; inset: 0; }
  .front__info {
    position: absolute; left: 30px; top: 40px; width: 260px;
    color: var(--white);
  }
  .brand-name {
    font-weight: 900; font-size: 23px; letter-spacing: -0.2px; line-height: 1;
    white-space: nowrap;
  }
  .brand-tagline {
    margin-top: 4px;
    font-family: "Roboto Mono", monospace; font-weight: 500;
    font-size: 7.4px; letter-spacing: 1.6px; text-transform: uppercase;
    color: var(--sky); white-space: nowrap;
  }
  .person-name { margin-top: 24px; font-size: 21px; color: var(--sky); line-height: 1; }
  .person-title { margin-top: 4px; font-size: 13px; }
  .address { margin-top: 20px; font-size: 13px; line-height: 1.3; }
  .contacts { list-style: none; margin-top: 14px; font-size: 13px; line-height: 1.45; }
  .contacts li { display: flex; align-items: center; gap: 8px; }
  .contacts svg { width: 12px; height: 12px; flex: none; }

  /* back */
  .back__lockup {
    position: absolute; left: 60px; top: 118px;
    display: flex; align-items: center; gap: 12px;
    color: var(--purple-emboss);
  }
  .back__square { width: 40px; height: 40px; background: var(--purple-emboss); }
  .back__lockup .brand-name { font-size: 30px; }
  .back__lockup .brand-tagline { color: var(--purple-emboss); font-size: 8.6px; letter-spacing: 2.4px; }
</style>
</head>
<body>
<main class="stage">

  <section class="card card--front" aria-label="Business card front">
    <svg class="front__panel" viewBox="0 0 520 297" width="520" height="297" aria-hidden="true">
      <defs>
        <linearGradient id="markTones" x1="0" y1="0" x2="1" y2="1">
          <stop offset="0" stop-color="#f08c1e"/>
          <stop offset="0.35" stop-color="#86bf3b"/>
          <stop offset="0.7" stop-color="#00a8e4"/>
          <stop offset="1" stop-color="#6f3391"/>
        </linearGradient>
      </defs>
      <polygon points="300,0 520,0 520,297 382,297" fill="#ffffff"/>
      <polygon points="310,0 520,0 520,297 392,297" fill="url(#markTones)"
               role="img" aria-label="Large brand mark decoration"/>
    </svg>
    <div class="front__info">
      <p class="brand-name">Orin Behavioral Health</p>
      <p class="brand-tagline">Committed to calm, care and renewal</p>
      <p class="person-name">Daniel Hale</p>
      <p class="person-title">Manager</p>
      <p class="address">Your address, city<br>state, ZIP 0000</p>
      <ul class="contacts">
        <li>
          <svg viewBox="0 0 24 24" aria-hidden="true"><path fill="#00a8e4" d="M6.6 10.8a15.1 15.1 0 0 0 6.6 6.6l2.2-2.2a1 1 0 0 1 1-.25 11.4 11.4 0 0 0 3.6.57 1 1 0 0 1 1 1V20a1 1 0 0 1-1 1A17 17 0 0 1 3 4a1 1 0 0 1 1-1h3.5a1 1 0 0 1 1 1c0 1.25.2 2.45.57 3.57a1 1 0 0 1-.25 1z"/></svg>
          555-014-2100
        </li>
        <li>
          <svg viewBox="0 0 24 24" aria-hidden="true"><rect x="2" y="5" width="20" height="14" fill="none" stroke="#00a8e4" stroke-width="2"/><path d="M2 5l10 8 10-8" fill="none" stroke="#00a8e4" stroke-width="2"/></svg>
          contact@orinhealth.com
        </li>
        <li>
          <svg viewBox="0 0 24 24" aria-hidden="true"><circle cx="12" cy="12" r="10" fill="#00a8e4"/><path d="M2 12h20M12 2c3 3 3 17 0 20M12 2c-3 3-3 17 0 20" stroke="#6f3391" stroke-width="1.5" fill="none"/></svg>
          www.orinhealth.com
        </li>
      </ul>
    </div>
  </section>

  <section class="card card--back" aria-label="Business card back">
    <div class="back__lockup">
      <span class="back__square" aria-hidden="true"></span>
      <div>
        <p class="brand-name">Orin Behavioral Health</p>
        <p class="brand-tagline">Committed to calm, care and renewal</p>
      </div>
    </div>
  </section>

</main>
</body>
</html>
```